QP Fiduciary Website Redesign Contest

We want to refresh our website to be more insitutional, professional for an international audience. We have designed a new logo for this purpose and that has been attached. A full brand brief and positioning statement has also been attached. Please read through all the documents carefully before designing. The old website is found here: https://qp-fiduciary.example/

Target Market(s)

Actuaries and associated businesses internationally

Industry/Entity Type

professional services - actuaries

Number of Pages Required

3 page

Font styles to use
Sans Serif

Colors
0054AA
0677BA
7BADD7
CADEEF
E8F1F8
0094D4
00A9DD
6FCCEA
C7EBF8
E9F6FB
F0912C
F2A743
F7CA91
FBE8D2
FDF5EE
EE7325
F08F49
F5BC92
FAE3D3
FDF4ED
EB3D1F
EC4F4E
F09395
F8D3D4
FCEDEE

Requirements
Must have
• blues and greens to match the logo color, complimentary colors, navigation
Nice to have
• old site: https://qp-fiduciary.example/

```html
<!DOCTYPE html>
<html lang="en">
<head>
<meta charset="utf-8">
<title>QP Fiduciary — Actuarial Software</title>
<link href="https://fonts.googleapis.com/css2?family=Orbitron:wght@400;600;700;800&family=Poppins:wght@400;500;600;700&display=swap" rel="stylesheet">
<style>
:root{
  --navy:#0b1635;
  --ink:#1b1f2a;
  --muted:#4a4f5c;
  --orange:#EE7325;
  --orange-lt:#F08F49;
  --blue:#0054AA;
  --blue-mid:#0677BA;
  --teal:#12a88e;
  --sky:#E8F1F8;
  --sky2:#E9F6FB;
  --white:#ffffff;
  --display:'Orbitron', sans-serif;
  --body:'Poppins', sans-serif;
}
*{box-sizing:border-box;margin:0;padding:0}
html,body{width:1200px;height:4342px;overflow:hidden}
body{font-family:var(--body);color:var(--ink);background:var(--white);position:relative}
.abs{position:absolute}
section,header,footer{position:absolute;left:0;width:1200px}

/* header */
.site-header{top:0;height:70px;background:#fff}
.brand{left:70px;top:18px;font-family:var(--body);font-weight:700;font-size:26px;color:var(--navy);letter-spacing:1px}
.main-nav{left:390px;top:26px;display:flex;gap:31px;font-size:13px}
.main-nav a{color:var(--ink);text-decoration:none}
.main-nav a.active{color:var(--blue-mid)}
.btn-orange{background:var(--orange);color:#fff;border-radius:22px;font-weight:500;text-decoration:none;display:flex;align-items:center;justify-content:center}
.header-cta{left:875px;top:17px;width:253px;height:37px;font-size:13px}

/* hero */
.hero{top:70px;height:544px;background:linear-gradient(100deg,#1a222e 0%,#2a3444 40%,#6f7c8e 75%,#c8d0da 100%)}
.hero-title{left:70px;top:118px;font-family:var(--display);font-size:32px;line-height:43px;color:#fff;font-weight:400;letter-spacing:1px}
.hero-title b{font-weight:800}
.hero-lead{left:72px;top:300px;width:470px;font-size:13.5px;line-height:22px;color:#e9edf3}
.hero-cta{left:70px;top:376px;width:325px;height:43px;font-size:14px;justify-content:space-between;padding:0 6px 0 22px}
.arrow-dot{width:32px;height:32px;border-radius:50%;background:#fff;display:flex;align-items:center;justify-content:center}

/* section headings */
.sec-title{left:0;width:1200px;text-align:center;font-family:var(--display);font-size:33px;letter-spacing:2px;color:var(--navy);font-weight:600}
.sec-sub{left:0;width:1200px;text-align:center;font-size:12.5px;line-height:21px;color:var(--ink)}

/* overview */
.overview{top:614px;height:529px;background:#fff}
.feature-card{width:212px;height:222px;border-radius:14px;background:linear-gradient(180deg,#eef8f6,#f3f7fb);box-shadow:0 8px 22px rgba(40,80,120,.12);text-align:center;padding:38px 14px 0}
.feature-card h3{font-size:15.5px;font-weight:500;margin:18px 0 6px;line-height:21px}
.feature-card p{font-size:11px;line-height:18px;color:var(--muted)}
.feature-card.is-featured{background:linear-gradient(135deg,#12a88e,#0054AA);color:#fff}
.feature-card.is-featured p{color:#d9ecf7}

/* core solutions */
.core{top:1143px;height:837px;background:var(--sky)}
.solution-board{left:142px;top:169px;width:914px;height:583px;background:#fff;border-radius:12px 110px 110px 110px;overflow:hidden;border:1px solid #dfe6ee}
.solution-photo{left:0;top:0;width:458px;height:291px;background:linear-gradient(135deg,#3a4658,#8c9aab 55%,#dfe5ec)}
.solution{text-align:center}
.solution h3{font-size:20px;font-weight:600;margin:12px 0 10px}
.solution p{font-size:12.5px;line-height:21px;color:var(--muted)}
.btn-outline{display:inline-block;margin-top:16px;border:1px solid var(--orange);color:var(--orange);font-size:12px;padding:8px 17px;border-radius:5px}
.board-mark{left:415px;top:234px;width:110px;height:110px;border-radius:50%;background:#fff;box-shadow:0 6px 18px rgba(0,0,0,.12);display:flex;align-items:center;justify-content:center;font-weight:700;font-size:24px;color:var(--navy)}

/* characteristics */
.traits{top:1980px;height:646px;background:#fff}
.trait-label{width:180px;text-align:center;font-size:15.5px;font-weight:500;line-height:21px}
.btn-teal{background:linear-gradient(90deg,#12a88e,#0054AA);color:#fff;border-radius:24px;font-size:12px;display:flex;align-items:center;justify-content:space-between;padding:0 6px 0 16px;letter-spacing:.3px}

/* insights */
.insights{top:2626px;height:794px;background:var(--sky)}
.post{width:284px;height:422px;background:#fff;border-radius:12px;box-shadow:0 6px 20px rgba(30,60,100,.08);padding:10px}
.post-img{height:205px;border-radius:10px}
.post-date{margin:20px 0 0 8px;font-size:11.5px;display:flex;align-items:center;gap:6px}
.post h4{margin:10px 8px 0;font-size:14px;line-height:21px;font-weight:600}
.post p{margin:3px 8px 0;font-size:12.5px;line-height:21px;color:var(--muted)}
.post .btn-outline{margin:14px 0 0 8px}
.slider-arrow{width:36px;height:36px;border-radius:50%;display:flex;align-items:center;justify-content:center}

/* cta */
.cta{top:3420px;height:575px;background:#fff}
.cta-banner{left:140px;top:85px;width:918px;height:365px;border-radius:40px 12px 40px 12px;background:linear-gradient(100deg,#12a88e 0%,#0a8ca3 45%,#0054AA 100%)}
.cta-title{left:140px;top:148px;width:918px;text-align:center;font-family:var(--display);font-size:33px;line-height:46px;letter-spacing:2px;color:#fff}
.cta-text{left:140px;top:246px;width:918px;text-align:center;font-size:12.5px;line-height:21px;color:#e8f3fb}
.btn-white{left:450px;top:332px;width:305px;height:41px;background:#fff;border-radius:22px;font-size:12px;display:flex;align-items:center;justify-content:space-between;padding:0 5px 0 16px;color:var(--ink)}
.cta-photo{background:linear-gradient(135deg,#3e4a5c,#b8c3cf)}

/* footer */
.site-footer{top:3995px;height:347px;background:var(--navy);color:#d7dcea}
.footer-brand{left:143px;top:60px;font-weight:700;font-size:24px;color:#fff;letter-spacing:1px}
.footer-about{left:141px;top:110px;width:225px;font-size:11.5px;line-height:19.5px}
.footer-col h5{font-family:var(--display);font-weight:400;font-size:13px;letter-spacing:1px;color:#fff;margin-bottom:10px}
.footer-col li{list-style:none;font-size:12.5px;line-height:28px}
.contact-item{display:flex;gap:8px;font-size:12px;line-height:20px;margin-bottom:12px}
.social-item{display:flex;align-items:center;gap:10px;font-size:12.5px;margin-bottom:13px}
.social-dot{width:28px;height:28px;border-radius:50%;border:1.5px solid #fff}
.social-dot.on{background:#12a88e;border-color:#12a88e}
.footer-rule{left:140px;top:290px;width:920px;height:1px;background:#2c3a5e}
.footer-bottom{left:140px;top:313px;width:920px;display:flex;justify-content:space-between;font-size:12px}
</style>
</head>
<body>

<header class="site-header">
  <div class="abs brand">QP FIDUCIARY</div>
  <nav class="abs main-nav">
    <a class="active" href="#">Home</a><a href="#">Platform</a><a href="#">Solutions</a><a href="#">Insights</a><a href="#">Company</a><a href="#">Contact</a>
  </nav>
  <a class="abs btn-orange header-cta" href="#">Request a Technical Walkthrough</a>
</header>

<section class="hero" role="img" aria-label="Photo of a businessman in a suit holding a tablet showing financial charts">
  <h1 class="abs hero-title">ACTUARIAL SOFTWARE<br>FOR <b>STRUCTURED,<br>AUDITABLE FINANCIAL<br>ANALYSIS.</b></h1>
  <p class="abs hero-lead"><b>QP Fiduciary</b> develops software that translates established actuarial methodologies into disciplined, decision-ready tools.</p>
  <a class="abs btn-orange hero-cta" href="#">Request A Technical Walkthrough <span class="arrow-dot"><svg width="16" height="16" viewBox="0 0 16 16"><path d="M3 8h10M9 4l4 4-4 4" stroke="#EE7325" stroke-width="2" fill="none"/></svg></span></a>
</section>

<section class="overview">
  <h2 class="abs sec-title" style="top:74px">PLATFORM OVERVIEW</h2>
  <p class="abs sec-sub" style="top:136px">Our Platform Delivers Structured Workflows, Transparent Assumptions, And Complete Auditability<br>—Enabling Confident, Governance-Ready Financial Analysis.</p>

  <div class="abs feature-card" style="left:140px;top:221px">
    <svg width="60" height="46" viewBox="0 0 60 46"><rect x="4" y="2" width="40" height="26" rx="3" fill="none" stroke="#0677BA" stroke-width="3"/><rect x="12" y="32" width="12" height="10" fill="#12a88e"/><rect x="30" y="32" width="12" height="10" fill="#0677BA"/><rect x="46" y="32" width="12" height="10" fill="#12a88e"/><path d="M10 10h28M10 17h18" stroke="#12a88e" stroke-width="3"/></svg>
    <h3>Structured Workflows</h3>
    <p>Disciplined Processes That Guide Analysis From Input To Output With Clear, Repeatable Steps.</p>
  </div>
  <div class="abs feature-card is-featured" style="left:377px;top:216px">
    <svg width="60" height="54" viewBox="0 0 60 54"><circle cx="28" cy="30" r="20" fill="none" stroke="#fff" stroke-width="3"/><circle cx="38" cy="18" r="12" fill="#fff"/></svg>
    <h3 style="margin-top:10px">Transparency<br>of Assumptions</h3>
    <p>Every Assumption Is Documented, Visible, And Traceable Throughout...</p>
  </div>
  <div class="abs feature-card" style="left:612px;top:221px">
    <svg width="50" height="50" viewBox="0 0 50 50"><rect x="6" y="2" width="30" height="40" rx="3" fill="none" stroke="#0677BA" stroke-width="3"/><circle cx="32" cy="34" r="11" fill="#12a88e"/><path d="M27 34l4 4 6-7" stroke="#fff" stroke-width="2.5" fill="none"/><path d="M12 12h18M12 20h14" stroke="#0677BA" stroke-width="3"/></svg>
    <h3>Auditability</h3>
    <p>Complete Audit Trails With Version Control And Comprehensive Documentation At Every Step.</p>
  </div>
  <div class="abs feature-card" style="left:848px;top:221px">
    <svg width="54" height="50" viewBox="0 0 54 50"><circle cx="34" cy="16" r="11" fill="none" stroke="#0677BA" stroke-width="5" stroke-dasharray="5 3"/><rect x="6" y="28" width="8" height="18" fill="#12a88e"/><rect x="18" y="22" width="8" height="24" fill="#0677BA"/><rect x="30" y="32" width="8" height="14" fill="#12a88e"/></svg>
    <h3>Governance</h3>
    <p>Built-In Controls And Approval Workflows That Ensure Regulatory Compliance.</p>
  </div>
</section>

<section class="core">
  <h2 class="abs sec-title" style="top:52px">CORE SOLUTIONS</h2>
  <p class="abs sec-sub" style="top:108px">Three Integrated Solution Areas Designed To Address The Full Spectrum Of Actuarial Analysis Needs.</p>

  <div class="abs solution-board">
    <div class="abs solution-photo" role="img" aria-label="Photo of colleagues reviewing bar charts on a laptop and printed reports"></div>
    <div class="abs" style="left:457px;top:0;width:1px;height:583px;background:#dfe6ee"></div>
    <div class="abs" style="left:0;top:291px;width:914px;height:1px;background:#dfe6ee"></div>

    <div class="abs solution" style="left:458px;top:32px;width:456px">
      <svg width="64" height="62" viewBox="0 0 64 62"><rect x="14" y="4" width="34" height="44" rx="3" fill="none" stroke="#0054AA" stroke-width="3"/><path d="M20 14h22M20 22h16M20 30h20" stroke="#0677BA" stroke-width="3"/><circle cx="48" cy="46" r="11" fill="#0054AA"/><rect x="4" y="40" width="14" height="16" fill="#0677BA"/></svg>
      <h3>Reserving &amp; Valuation</h3>
      <p>Comprehensive reserve calculations and liability<br>valuations with transparent methodology<br>documentation and multi-standard support.</p>
      <span class="btn-outline">READ MORE</span>
    </div>
    <div class="abs solution" style="left:0;top:318px;width:458px">
      <svg width="64" height="58" viewBox="0 0 64 58"><rect x="6" y="20" width="52" height="32" rx="6" fill="none" stroke="#0054AA" stroke-width="3"/><rect x="22" y="4" width="22" height="22" rx="3" transform="rotate(20 33 15)" fill="#0677BA"/><circle cx="20" cy="40" r="5" fill="#0054AA"/><circle cx="44" cy="40" r="5" fill="#0054AA"/></svg>
      <h3>Pricing</h3>
      <p>Sophisticated pricing models that balance<br>profitability targets with competitive positioning<br>and regulatory requirements.</p>
      <span class="btn-outline">READ MORE</span>
    </div>
    <div class="abs solution" style="left:458px;top:314px;width:456px">
      <svg width="66" height="60" viewBox="0 0 66 60"><circle cx="40" cy="20" r="13" fill="none" stroke="#0054AA" stroke-width="5" stroke-dasharray="6 3"/><path d="M6 52l12-20 12 20z" fill="#0677BA"/><path d="M18 40v5" stroke="#fff" stroke-width="2.5"/><path d="M34 50c8 0 16-4 24-10" stroke="#0054AA" stroke-width="4" fill="none"/></svg>
      <h3>Enterprise Risk Management</h3>
      <p>Holistic risk assessment and capital modeling<br>that integrates across business units and<br>regulatory frameworks.</p>
      <span class="btn-outline">READ MORE</span>
    </div>
    <div class="abs board-mark">QP</div>
  </div>
</section>

<section class="traits">
  <h2 class="abs sec-title" style="top:78px">PLATFORM CHARACTERISTICS</h2>
  <p class="abs sec-sub" style="top:134px">Key Attributes That Set Our Platform Apart In Delivering Reliable, Governance-Ready<br>Actuarial Analysis.</p>

  <svg class="abs" style="left:130px;top:190px" width="940" height="290" viewBox="0 0 940 290">
    <defs>
      <linearGradient id="bandTeal" x1="0" y1="0" x2="0" y2="1"><stop offset="0" stop-color="#a8e0d5"/><stop offset="1" stop-color="#d5eef0"/></linearGradient>
      <linearGradient id="bandBlue" x1="0" y1="0" x2="0" y2="1"><stop offset="0" stop-color="#bfd5ea"/><stop offset="1" stop-color="#9fc0e0"/></linearGradient>
      <filter id="hexShadow" x="-20%" y="-20%" width="140%" height="140%"><feDropShadow dx="0" dy="6" stdDeviation="7" flood-color="#5a7088" flood-opacity=".22"/></filter>
    </defs>
    <path d="M12 84 Q12 70 24 63 L112 12 Q138 -2 164 12 L240 56 L240 180 L12 180 Z" fill="url(#bandTeal)"/>
    <path d="M200 200 L320 268 Q360 290 400 268 L460 234 L460 140 L200 140 Z" fill="url(#bandTeal)"/>
    <path d="M420 84 L540 14 Q578 -6 616 14 L700 62 L700 190 L420 190 Z" fill="url(#bandBlue)"/>
    <path d="M660 180 L780 258 Q816 280 852 258 L920 218 Q928 212 928 200 L928 96 L660 96 Z" fill="url(#bandBlue)"/>
    <g filter="url(#hexShadow)" fill="#fff">
      <path d="M138 46 Q148 40 158 46 L220 82 Q230 88 230 100 L230 170 Q230 182 220 188 L158 224 Q148 230 138 224 L76 188 Q66 182 66 170 L66 100 Q66 88 76 82 Z"/>
      <path d="M360 46 Q370 40 380 46 L442 82 Q452 88 452 100 L452 170 Q452 182 442 188 L380 224 Q370 230 360 224 L298 188 Q288 182 288 170 L288 100 Q288 88 298 82 Z"/>
      <path d="M580 46 Q590 40 600 46 L662 82 Q672 88 672 100 L672 170 Q672 182 662 188 L600 224 Q590 230 580 224 L518 188 Q508 182 508 170 L508 100 Q508 88 518 82 Z"/>
      <path d="M798 46 Q808 40 818 46 L880 82 Q890 88 890 100 L890 170 Q890 182 880 188 L818 224 Q808 230 798 224 L736 188 Q726 182 726 170 L726 100 Q726 88 736 82 Z"/>
    </g>
    <g>
      <circle cx="148" cy="86" r="13" fill="none" stroke="#0054AA" stroke-width="4"/><path d="M148 100v10M124 110h48M124 110v10M172 110v10" stroke="#0054AA" stroke-width="3" fill="none"/><rect x="116" y="118" width="16" height="10" fill="#12a88e"/><rect x="164" y="118" width="16" height="10" fill="#12a88e"/>
      <circle cx="370" cy="88" r="14" fill="none" stroke="#0054AA" stroke-width="5" stroke-dasharray="5 3"/><path d="M344 118c10-8 22-8 32 0 10 6 20 6 28 0" stroke="#12a88e" stroke-width="5" fill="none"/>
      <path d="M574 118v-22c0-16 14-26 28-22 12 4 16 16 10 26" stroke="#0054AA" stroke-width="4" fill="none"/><circle cx="596" cy="94" r="8" fill="#12a88e"/>
      <rect x="782" y="98" width="7" height="22" fill="#0677BA"/><rect x="794" y="88" width="7" height="32" fill="#12a88e"/><rect x="806" y="102" width="7" height="18" fill="#0677BA"/><circle cx="822" cy="108" r="10" fill="none" stroke="#0054AA" stroke-width="4"/><path d="M829 115l8 8" stroke="#0054AA" stroke-width="4"/>
    </g>
  </svg>
  <div class="abs trait-label" style="left:178px;top:348px">Structured<br>Workflows</div>
  <div class="abs trait-label" style="left:400px;top:348px">Multi-Jurisdictional<br>Review Support</div>
  <div class="abs trait-label" style="left:620px;top:344px">Transparent<br>Assumptions</div>
  <div class="abs trait-label" style="left:838px;top:342px">Comparative<br>Analysis Capability</div>

  <a class="abs btn-teal" style="left:447px;top:512px;width:305px;height:43px" href="#">REQUEST A TECHNICAL WALKTHROUGH <span class="arrow-dot"><svg width="18" height="16" viewBox="0 0 18 16"><path d="M2 8h13M10 3l5 5-5 5" stroke="#0b1635" stroke-width="2" fill="none"/></svg></span></a>
</section>

<section class="insights">
  <h2 class="abs sec-title" style="top:88px">INSIGHTS &amp; THOUGHT</h2>
  <p class="abs sec-sub" style="top:154px">Key Attributes That Set Our Platform Apart In Delivering Reliable, Governance-<br>Ready Actuarial Analysis.</p>

  <div class="abs slider-arrow" style="left:75px;top:460px;border:1.5px solid #0b1635"><svg width="14" height="12" viewBox="0 0 14 12"><path d="M13 6H2M6 1L1 6l5 5" stroke="#0b1635" stroke-width="1.8" fill="none"/></svg></div>
  <div class="abs slider-arrow" style="left:1089px;top:460px;background:var(--blue-mid)"><svg width="14" height="12" viewBox="0 0 14 12"><path d="M1 6h11M8 1l5 5-5 5" stroke="#fff" stroke-width="1.8" fill="none"/></svg></div>

  <article class="abs post" style="left:140px;top:214px">
    <div class="post-img" role="img" aria-label="Illustration of business people at a table beneath a glowing lightbulb" style="background:linear-gradient(135deg,#0b1a4a,#1f5fa8 55%,#7ab8e8)"></div>
    <div class="post-date"><svg width="14" height="14" viewBox="0 0 14 14"><rect x="1" y="2" width="12" height="11" fill="#0054AA"/><path d="M3 6h8" stroke="#fff"/></svg>24 JUL 2025</div>
    <h4>RBC (Risk-Based Capital)</h4>
    <p>Harbor Point, 24 July 2025 – QP Fiduciary is an independent actuarial consulting firm headquartered...</p>
    <span class="btn-outline">READ MORE</span>
  </article>
  <article class="abs post" style="left:455px;top:214px">
    <div class="post-img" role="img" aria-label="Photo of a hand in a suit touching a rising financial chart" style="background:linear-gradient(135deg,#2a2f3a,#8a5a4a 50%,#d9dde3)"></div>
    <div class="post-date"><svg width="14" height="14" viewBox="0 0 14 14"><rect x="1" y="2" width="12" height="11" fill="#0054AA"/><path d="M3 6h8" stroke="#fff"/></svg>13 JAN 2026</div>
    <h4>Evolution into Technology-Led<br>Actuarial Platform</h4>
    <p>Harbor Point, January 12, 2026 – QP Fiduciary is thrilled...</p>
    <span class="btn-outline">READ MORE</span>
  </article>
  <article class="abs post" style="left:776px;top:214px">
    <div class="post-img" role="img" aria-label="Illustration of a digital accounting standards interface with gears" style="background:linear-gradient(135deg,#0e2a44,#2a6f8f 55%,#a7d6e8)"></div>
    <div class="post-date"><svg width="14" height="14" viewBox="0 0 14 14"><rect x="1" y="2" width="12" height="11" fill="#0054AA"/><path d="M3 6h8" stroke="#fff"/></svg>17 JAN 2025</div>
    <h4>IFRS 17: A Paradigm Shift For<br>Insurers</h4>
    <p>Harbor Point, January 17, 2025 – QP Fiduciary is an actuarial consulting...</p>
    <span class="btn-outline">READ MORE</span>
  </article>

  <a class="abs btn-teal" style="left:510px;top:668px;width:180px;height:42px" href="#">VIEW ALL ARTICLES <span class="arrow-dot"><svg width="18" height="16" viewBox="0 0 18 16"><path d="M2 8h13M10 3l5 5-5 5" stroke="#0b1635" stroke-width="2" fill="none"/></svg></span></a>
</section>

<section class="cta">
  <div class="abs cta-banner"></div>
  <div class="abs cta-photo" role="img" aria-label="Photo of a laptop showing charts with hands pointing at the screen" style="left:113px;top:180px;width:210px;height:300px;border-radius:110px 20px 110px 110px"></div>
  <div class="abs cta-photo" role="img" aria-label="Photo of colleagues reviewing printed charts at a desk" style="left:843px;top:222px;width:260px;height:235px;border-radius:110px 20px 30px 30px;background:linear-gradient(135deg,#9aa7b7,#e6ebf0)"></div>
  <h2 class="abs cta-title">READY TO TRANSFORM YOUR<br>ACTUARIAL PRACTICE?</h2>
  <p class="abs cta-text">Discover How QP Fiduciary's Platform Can Bring Structure,<br>Transparency, And Confidence To Your Financial Analysis Workflows.</p>
  <a class="abs btn-white" href="#">REQUEST A TECHNICAL WALKTHROUGH <span class="arrow-dot" style="background:#0677BA"><svg width="18" height="16" viewBox="0 0 18 16"><path d="M2 8h13M10 3l5 5-5 5" stroke="#fff" stroke-width="2" fill="none"/></svg></span></a>
</section>

<footer class="site-footer">
  <div class="abs footer-brand">QP FIDUCIARY</div>
  <p class="abs footer-about">Common Approach To Service Delivery Can Be Described Within A Cycle That Involves Defining The Problem, Designing A Solution And Monitoring The Results:</p>

  <div class="abs footer-col" style="left:463px;top:58px">
    <h5>QUICK LINKS</h5>
    <ul><li>Company</li><li>Platform</li><li>Solutions</li><li>Insights</li><li>Contact</li></ul>
  </div>

  <div class="abs footer-col" style="left:662px;top:58px;width:200px">
    <h5>CONTACT DETAILS</h5>
    <div class="contact-item"><svg width="12" height="16" viewBox="0 0 12 16"><path d="M6 15S1 9 1 6a5 5 0 0110 0c0 3-5 9-5 9z" fill="#fff"/><circle cx="6" cy="6" r="2" fill="#0b1635"/></svg><span>410 Meridian Park Ave,<br>Suite 200<br>Harbor Point, FL 30000</span></div>
    <div class="contact-item"><svg width="12" height="14" viewBox="0 0 12 14"><path d="M2 1l3 0 1 3-2 1c1 2 2 3 4 4l1-2 3 1v3c-6 1-11-4-10-10z" fill="#fff"/></svg><span>Phone<br>+1(555)010-2040</span></div>
    <div class="contact-item"><svg width="13" height="12" viewBox="0 0 13 12"><rect x="0" y="1" width="13" height="10" fill="#fff"/><path d="M0 1l6.5 5L13 1" stroke="#0b1635" fill="none"/></svg><span>Email<br>hello@qp-fiduciary.example</span></div>
  </div>

  <div class="abs footer-col" style="left:933px;top:58px">
    <h5>SOCIAL MEDIA</h5>
    <div class="social-item"><span class="social-dot on"></span>Community</div>
    <div class="social-item"><span class="social-dot"></span>Video Channel</div>
    <div class="social-item"><span class="social-dot"></span>Pro Network</div>
    <div class="social-item"><span class="social-dot"></span>Photo Feed</div>
  </div>

  <div class="abs footer-rule"></div>
  <div class="abs footer-bottom"><span>© 2026 QP Fiduciary All Rights Reserved.</span><span>Price Policy&nbsp; Terms And Conditions</span></div>
</footer>

</body>
</html>
```